Packaging Design for Health/Beauty product

This project is for the brand new design of our new product.
Box/Tube/Images
The product is an anesthetic Skin Numbing Cream used for numbing skin for general pain relief and also before tattoos, waxing, laser hair removal and small cosmetic procedures.
Direct to end user and also to salons and studios, with view to selling in pharmacies.
This is a Brand New Product
Packaging design for the brand CALORVEX
2 components -
1. TUBE/OUTER PACKAGING design
and
2. "3D" style graphics/images suitable for marketing
******************
DELIVERABLES:
Tube:
Adobe Illustrator file (.ai) using supplied template for die lines prior to printing/manufacture and PDF files
PNG files for 3D style renderings of front, back, side, and angled left and right.
Outer Packaging:
PNG files for some 3D style renderings of front, back, side, and angled left and right.
******************
WHAT IS THE PRODUCT?
It is an anesthetic skin numbing cream, with Aloe for soothing the skin and Tea Tree
Please google “numbing cream”- images and you’ll get an idea of the 3D styling required.
But - please think “outside the box” and design something that is NOT a copy or modelled off existing brands. We want something completely new to stand out from the crowd without being too "Over The Top."
Keep the core demographic in mind.
This job had previously been given to an artist on here, but prior to completion he ceased replying to my emails. I have a #D image of what we were after.
You may either replicate what was done there (I only have a PDF image, no AI source files) OR you may go for a completely new design.
Both options will be given equal appraisal.
******************
DEMOGRAPHIC
The target market will be for pain relief for injection, vaccinations, waxing, laser hair removal - Mainly for 18-40 year olds, male/female. We also have a view to going into mainstream pharmacies as well.
We are after a visually striking design that will attract the eye and be appealing to our target market- but also a nice clean, uncluttered design.
******************
LOGO INCLUDED - Attachment
Supplied is our "Branding Logo" that is to be incorporated onto both the tube and outer packaging.
IF you have a completely different idea/color scheme that would incorporate a good logo (different than supplied) then that is also ok - it would require you to design the logo as well.
*******************
TEMPLATES - Attachment
2 Templates are supplied - 1 x Tube & 1 x Outer Package
It is for an FDA regulated drug.
The fonts/text on the templates are representative of the WORDING required.
Positioning within each panel can be altered to suit the design, this is for your guidance.
Bar code, NDC code, company logo and other required info will all be supplied.
Please also add a QR code as per the attached example form a different product
Your job is to come up with a great design.
Template provided in Adobe Illustrator (.ai) and must be delivered as same.
*********************
COLORS
Currently we have our logo in green/orange, and we think these neutral colors work well with this market.
As stated, IF you have a totally new idea for LOGO & DESIGN, feel free to use your skills!
Using extra colors comes down to your design, but keep in mind that too many colors can lose impact and not print well.
Remember this will be printed on a plastic tube and a cardboard outer packaging - so the design must be able to look good on a physical product.
Not just on a digital website.
********************
UNIQUE SELLING POINT
Our cream has both Tea Tree & Aloe in the ingredients, and if they can be highlighted in some visual way without detracting from the overall design that would be great.
Use your skills here to represent this as best you can without making it be the main focus.
********************
DRUG FACTS PANEL
Within the supplied templates is a drug facts label that will require some small text changes. WE will make those changes and forward the updated Drug Facts Panel to you.
However the existing panel DIMENSIONS within the template will not change, so you can go ahead and make your design, and we will forward the updated panel asap.
*******************
BARCODE - Attachment
Supplied is a barcode to be used as per template
Please also add a QR Code
******************
NDC CODE - a string of numbers eg/ 12345 678 90
We are still awaiting the receipt of the NDC code, and it may not arrive until after the contest is complete and the winner chosen, and the final adjustments to design made.
Please go ahead and do the main outlay. Upon receipt of the NDC I will send to you for insertion as necessary, wherein the job will be essentially finished.
Then I will need to 2D ai files and PDF templates for submission for registration, AND then also the 3D images that will have the NDC on them, exactly as the package will look once complete.
****************
3D RENDERS
I will need several HIGH QUALITY 3D images for use on our website and in marketing.
Images of the tube (different angles), the box, front and back (different angles), the tube coming out of the opened box, (different angles) - you get the idea what I need.
****************
IMPORTANT
We do not want any photos of people incorporated into the design.
We do not have a blank "3D" style tube for you to use to wrap your label around when creating the promotion style images.
I am awaiting from the manufacturer the final shaping of the tube (it will be similar to the graphic provided) BUT the cap will change shape due to new FDA Rules. Once I have that I will inform you. For now it is ok to use a simple screw cap, but please note that this will need to be changed before final sign off.
Please do your very best to create a great design.
Good luck and may the best design win!
Thankyou very much.

```html
<!DOCTYPE html>
<html lang="en">
<head>
<meta charset="utf-8">
<title>CALORVEX Numbing Cream Carton</title>
<link href="https://fonts.googleapis.com/css2?family=Oswald:wght@200;300;400&family=Arimo:wght@400&display=swap" rel="stylesheet">
<style>
  :root {
    --stage: #e9e9f0;
    --carton: #ffffff;
    --brand-blue: #2f2fa0;
    --ink: #141414;
    --muted: #6a6a78;
    --label-blue: #3a5fb0;
    --petal-deep: #5a4fc8;
    --petal-light: #c9cdf2;
    --leaf: #8cc63f;
  }
  * { box-sizing: border-box; margin: 0; padding: 0; }
  html, body { width: 1200px; height: 675px; overflow: hidden; }
  body {
    background: var(--stage);
    font-family: "Oswald", "Arial Narrow", sans-serif;
    display: flex; align-items: center; justify-content: center;
  }
  .carton {
    position: relative;
    width: 620px; height: 640px;
    background: var(--carton);
    box-shadow: 0 6px 24px rgba(60,60,90,.12);
  }
  .hang-tab {
    position: absolute; top: 0; left: 0; right: 0; height: 250px;
    border-radius: 18px 18px 0 0;
  }
  .hang-slot {
    position: absolute; top: 48px; left: 50%; transform: translateX(-50%);
    width: 150px; height: 30px; border-radius: 14px;
    background: var(--stage);
  }
  .ndc {
    position: absolute; top: 58px; right: 26px;
    font-family: "Arimo", Arial, sans-serif; font-size: 10px; color: var(--ink);
  }
  .brand {
    position: absolute; top: 138px; left: 70px;
    display: flex; align-items: center; gap: 14px;
  }
  .brand-dot { width: 22px; height: 22px; border-radius: 50%; background: var(--leaf); }
  .brand-name {
    font-weight: 400; font-size: 64px; letter-spacing: 3px;
    color: var(--brand-blue); line-height: 1;
  }
  .top-face {
    position: absolute; top: 250px; left: 0; right: 0; height: 90px;
  }
  .top-flowers {
    position: absolute; left: 0; top: 30px; width: 300px; height: 60px;
    background: radial-gradient(ellipse at 30% 60%, var(--petal-deep) 0%, var(--petal-light) 45%, rgba(255,255,255,0) 75%);
    opacity: .8;
  }
  .claims {
    position: absolute; right: 26px; top: 10px; text-align: right;
    font-weight: 300; font-size: 13px; letter-spacing: 1.5px; color: var(--muted);
    line-height: 1.45;
  }
  .claims strong { color: var(--brand-blue); font-weight: 400; }
  .front-face {
    position: absolute; top: 340px; left: 0; right: 0; bottom: 0;
    border-top: 1px solid #eeeef4;
  }
  .net-wt {
    position: absolute; top: 10px; right: 26px;
    font-weight: 300; font-size: 11px; letter-spacing: 1px; color: var(--muted);
  }
  .headline {
    position: absolute; top: 70px; left: 30px;
    font-weight: 200; font-size: 54px; line-height: 1.12; color: var(--ink);
    letter-spacing: .5px;
  }
  .front-flowers {
    position: absolute; right: 0; top: 20px; width: 230px; height: 270px;
    background:
      radial-gradient(ellipse at 55% 40%, var(--petal-deep) 0%, rgba(90,79,200,.5) 35%, rgba(255,255,255,0) 70%),
      radial-gradient(ellipse at 40% 80%, var(--petal-light) 0%, rgba(255,255,255,0) 65%);
  }
  .active {
    position: absolute; left: 30px; bottom: 22px;
    font-family: "Arimo", Arial, sans-serif; color: var(--label-blue);
  }
  .active-name { font-size: 17px; }
  .active-type { font-size: 11px; }
</style>
</head>
<body>
  <main class="carton">
    <section class="hang-tab">
      <div class="hang-slot"></div>
      <p class="ndc">NDC# 00000-000-00</p>
      <div class="brand">
        <span class="brand-dot"></span>
        <span class="brand-name">CALORVEX</span>
      </div>
    </section>

    <section class="top-face">
      <div class="top-flowers" role="img" aria-label="Soft photo of blue and white star-shaped flowers"></div>
      <p class="claims">
        WORKS FAST FOR RELIEF<br>
        MADE WITH ALOE AND TEA TREE<br>
        NUMBS THE <strong>SKIN</strong> - SAFE AND SOOTHING
      </p>
    </section>

    <section class="front-face">
      <p class="net-wt">NET WT. 2.0 Oz. (56.7g)</p>
      <h1 class="headline">MEDICAL CREAM TO<br>NUMB THE SKIN</h1>
      <div class="front-flowers" role="img" aria-label="Photo of a cluster of violet-blue and white flowers with green stems"></div>
      <div class="active">
        <p class="active-name">Lidocaine 4%</p>
        <p class="active-type">Pain Relieving Cream</p>
      </div>
    </section>
  </main>
</body>
</html>
```